UL Aesthetic improvement on full website

brightneighbourhq.com
We need someone to improve the current website brightneighbourhq.com
Some designed to fail to follow isntruction and deliver. please find attached summary latest design requirement, please follow and read each of the requirements carefully and submit max two versions only. The winner would have to deliver within 5 days

Sample reference : velmorq.com/html/brightneighbour/#
(previous winner cant deliver)
*All of our wording and graphic content are updated, designer wouldn't involve in recreating any content.
Designer may use template or own material. delivery in html and implement on our WordPress server

please submit about us the project submission.
upon the winning, you have to maintain sub content / pages and submit the full site with your improved version of full websites including inner pages

Low design quality

Target Market(s)

general audience

Industry/Entity Type

social service

Number of Pages Required

5+ page

Requirements
Must have
• feeling and look similar to pobrix dot com
Nice to have
• extend the same style to other pages

```html
<!DOCTYPE html>
<html lang="en">
<head>
<meta charset="utf-8">
<title>Bright Neighbour — New Way Of Giving Social Inclusion</title>
<link rel="stylesheet" href="https://fonts.googleapis.com/css2?family=Montserrat:wght@400;500;600;700&family=Open+Sans:wght@400;600&display=swap">
<style>
:root{
  --coral:#f2575f;
  --coral-soft:#f7828a;
  --coral-pale:#fbd3d5;
  --ink:#1f1f24;
  --text:#4a4a52;
  --mist:#efeeef;
  --white:#ffffff;
  --night:#0c0c0e;
}
*{box-sizing:border-box;margin:0;padding:0}
html,body{width:1200px;height:3936px;overflow:hidden}
body{position:relative;background:var(--white);font-family:"Open Sans",Arial,sans-serif;color:var(--text)}
.abs{position:absolute}
h1,h2,h3,.nav,.btn{font-family:"Montserrat",Arial,sans-serif}
.accent{color:var(--coral)}
.btn{display:inline-block;border-radius:24px;font-size:15px;font-weight:500;text-decoration:none;text-align:center;white-space:nowrap}
.btn-solid{background:var(--coral);color:var(--white);padding:11px 28px;box-shadow:0 6px 14px rgba(242,87,95,.3)}
.btn-ghost{border:2px solid var(--coral);color:var(--coral);padding:9px 22px;background:var(--white)}
.btn-light{background:var(--white);color:var(--coral);padding:11px 26px}

/* header & hero */
.hero{left:0;top:0;width:1200px;height:680px;background:var(--mist)}
.hero-wave{left:0;top:480px;width:1200px;height:220px}
.brand{left:104px;top:26px;width:72px;height:72px;border-radius:50%;background:var(--coral);color:var(--white);font-family:"Montserrat",sans-serif;font-weight:700;font-size:10px;line-height:1.2;display:flex;align-items:center;justify-content:center;text-align:center}
.nav{left:290px;top:40px;width:810px;display:flex;align-items:center;justify-content:flex-end;gap:30px;font-size:14px;font-weight:500;color:var(--ink);white-space:nowrap}
.nav a{color:inherit;text-decoration:none}
.nav .current{color:var(--coral)}
.nav .btn{font-size:14px;padding-top:9px;padding-bottom:9px}
.nav .btn-solid{color:var(--white)}
.nav .btn-ghost{color:var(--coral)}
.hero-title{left:104px;top:292px;font-size:46px;line-height:1.18;font-weight:700;color:var(--ink);white-space:nowrap}
.hero-copy{left:104px;top:420px;width:360px;font-size:14px;line-height:1.6;color:var(--ink)}
.hero-cta{left:104px;top:494px}
.hero-art{left:640px;top:110px;width:420px;height:440px}

/* glance */
.glance-title{left:0;top:820px;width:1200px;text-align:center;font-size:36px;font-weight:600;color:var(--ink)}
.feature h3{font-size:24px;font-weight:600;color:var(--ink);margin-bottom:22px}
.feature p{font-size:14px;line-height:1.85;margin-bottom:26px}
.art{border-radius:8px}

/* cta band */
.cta-band{left:0;top:2470px;width:1200px;height:330px;background:linear-gradient(120deg,#f7727a 0%,#f2575f 45%,#ee4d58 100%);overflow:hidden}
.cta-band h2{position:absolute;left:0;top:90px;width:1200px;text-align:center;color:var(--white);font-size:38px;font-weight:700}
.cta-band p{position:absolute;left:0;top:150px;width:1200px;text-align:center;color:var(--white);font-size:16px;font-weight:600}
.cta-band .btn{position:absolute;left:530px;top:200px}

/* values */
.value{left:104px;display:flex;gap:28px;width:420px}
.value-icon{width:68px;height:68px;flex:none;border-radius:50%;background:var(--coral);display:flex;align-items:center;justify-content:center}
.value h3{font-size:24px;font-weight:600;color:var(--ink);margin-bottom:10px}
.value p{font-size:14px;line-height:1.6}
.value a{font-size:14px;color:var(--coral);text-decoration:none;display:block;margin-top:8px}

/* footer */
.footer{left:0;top:3340px;width:1200px;height:596px;background:var(--night)}
.footer-wave{left:0;top:3300px;width:1200px;height:140px}
.footer h2{position:absolute;left:0;top:150px;width:1200px;text-align:center;color:var(--white);font-size:44px;font-weight:700}
.footer .lead{position:absolute;left:0;top:220px;width:1200px;text-align:center;color:var(--white);font-size:15px}
.footer .btn{position:absolute;left:534px;top:262px}
.social{position:absolute;left:528px;top:320px;display:flex;gap:20px}
.social span{width:40px;height:40px;border:2px solid var(--white);border-radius:50%;display:block}
.copyright{position:absolute;left:0;top:410px;width:1200px;text-align:center;color:var(--white);font-size:14px}
.dots{position:absolute;left:0;top:60px;width:130px;height:200px}
</style>
</head>
<body>

<section class="hero abs" aria-label="Hero"></section>
<svg class="hero-wave abs" viewBox="0 0 1200 220" preserveAspectRatio="none" aria-hidden="true">
  <path d="M0 60 C 260 200 520 210 760 150 C 960 100 1080 140 1200 190 L1200 220 L0 220 Z" fill="var(--coral)"/>
  <path d="M0 100 C 280 220 560 220 800 170 C 980 130 1100 170 1200 210 L1200 220 L0 220 Z" fill="var(--white)"/>
</svg>

<div class="brand abs">BRIGHT<br>NEIGHBOUR</div>
<nav class="nav abs">
  <a class="current" href="#">Home</a>
  <a href="#">About Us</a>
  <a href="#">Our Story</a>
  <a href="#">Social Impact</a>
  <a href="#">Join Us</a>
  <a class="btn btn-solid" href="#">Book a Demo</a>
  <a class="btn btn-ghost" href="#">Login</a>
</nav>

<h1 class="hero-title abs"><span class="accent">New Way</span> Of Giving<br>Social Inclusion</h1>
<p class="hero-copy abs">Lorem ipsum dolor sit amet, consectetur adipiscing elit, sed do eiusmod tempor incididunt ut.</p>
<a class="btn btn-solid hero-cta abs" href="#">Learn More</a>
<div class="hero-art abs art" role="img" aria-label="Three smartphones showing the giving app on a coral blob" style="background:radial-gradient(circle at 50% 55%,var(--coral) 0 38%,transparent 39%),linear-gradient(180deg,#f4f4f4,#e6e6e6);border-radius:40px"></div>

<h2 class="glance-title abs">Bright Neighbour <span class="accent">At A Glance</span></h2>

<div class="abs art" role="img" aria-label="Smartphone showing listings of contributions over a coral blob" style="left:150px;top:940px;width:300px;height:440px;background:radial-gradient(ellipse at 45% 55%,var(--coral) 0 45%,transparent 46%),linear-gradient(#fafafa,#fafafa);border-radius:30px"></div>
<article class="feature abs" style="left:640px;top:1050px;width:420px">
  <h3>Contributors</h3>
  <p>You can pay-it-forward products and services listings on our platform just like any other e-commerce platform with a kind message. The platform will match with beneficiaries who require the contributions with the personalised kind message.</p>
  <a class="btn btn-solid" href="#">Learn More</a>
</article>

<article class="feature abs" style="left:112px;top:1580px;width:420px">
  <h3>Merchants</h3>
  <p>Our free listing platform allow merchants to upload and list the available goods and services. Beneficiary or their representative make the booking and contact the merchant to claim the contributions directly with redemption code verifications.</p>
  <a class="btn btn-solid" href="#">Learn More</a>
</article>
<div class="abs art" role="img" aria-label="Illustration of people stacking pastel blocks into a staircase" style="left:780px;top:1460px;width:360px;height:360px;background:linear-gradient(160deg,#fde4e6 0%,#f8c9d3 40%,#e4d6f4 70%,#fbe7b8 100%)"></div>

<div class="abs art" role="img" aria-label="Illustration of two people meeting on a bridge of pastel blocks" style="left:112px;top:1980px;width:370px;height:380px;background:linear-gradient(160deg,#fde4e6 0%,#e4d6f4 50%,#fbe7b8 100%)"></div>
<article class="feature abs" style="left:640px;top:2060px;width:440px">
  <h3>Community Partners</h3>
  <p>Our partners perform due diligence to verify cases and duration of support that needed. They are our link to society, managing the eligible beneficiaries directly with a flexible approach. Each beneficiary is registered with a secure ID. They have access to other pages with the ability to filter the types of contributions, availability, diet preferences, and distance.</p>
  <a class="btn btn-solid" href="#">Learn More</a>
</article>

<section class="cta-band abs">
  <svg class="abs" style="left:0;top:0" width="1200" height="330" viewBox="0 0 1200 330" aria-hidden="true">
    <path d="M0 0 L260 0 C 200 120 120 200 0 260 Z" fill="#ffffff" opacity=".12"/>
    <path d="M1200 330 L900 330 C 980 220 1080 140 1200 100 Z" fill="#ffffff" opacity=".12"/>
    <path d="M320 330 C 420 220 560 200 700 330 Z" fill="#ffffff" opacity=".06"/>
  </svg>
  <h2>Ready to get started?</h2>
  <p>See how TrackLume data can take your company further.</p>
  <a class="btn btn-light" href="#">Get Your Free Trial</a>
</section>

<div class="value abs" style="top:2890px">
  <div class="value-icon"><svg width="34" height="34" viewBox="0 0 24 24" fill="none" stroke="#fff" stroke-width="2"><circle cx="12" cy="12" r="9"/><path d="M12 7v5l3 3"/></svg></div>
  <div><h3>Our Philosophy</h3><p>We believe in authentic social responsibility is driven from</p><a href="#">Learn More</a></div>
</div>
<div class="value abs" style="top:3040px">
  <div class="value-icon"><svg width="34" height="34" viewBox="0 0 24 24" fill="none" stroke="#fff" stroke-width="2"><circle cx="12" cy="12" r="8"/><circle cx="12" cy="12" r="3"/></svg></div>
  <div><h3>Our Mission</h3><p>We connect individuals and businesses to support where it</p><a href="#">Learn More</a></div>
</div>
<div class="value abs" style="top:3190px">
  <div class="value-icon"><svg width="34" height="34" viewBox="0 0 24 24" fill="none" stroke="#fff" stroke-width="2"><path d="M4 18l6-6 4 4 6-8"/></svg></div>
  <div><h3>Our Future</h3><p>Together, social impact as part of DNA at the heart of every</p><a href="#">Learn More</a></div>
</div>
<div class="abs art" role="img" aria-label="Illustrated city skyline with people helping each other in a park" style="left:560px;top:2888px;width:608px;height:416px;background:linear-gradient(180deg,#cfe6f3 0%,#e9eef4 45%,#f7a7b0 75%,#f2787f 100%);border-radius:14px"></div>

<svg class="footer-wave abs" viewBox="0 0 1200 140" preserveAspectRatio="none" aria-hidden="true">
  <path d="M0 40 C 300 120 700 130 1200 40 L1200 140 L0 140 Z" fill="var(--night)"/>
</svg>
<footer class="footer abs">
  <svg class="dots" viewBox="0 0 130 200" aria-hidden="true">
    <g fill="#ffffff" opacity=".8">
      <circle cx="20" cy="20" r="3"/><circle cx="50" cy="20" r="3"/><circle cx="80" cy="20" r="3"/>
      <circle cx="20" cy="50" r="3"/><circle cx="50" cy="50" r="3"/><circle cx="80" cy="50" r="3"/>
      <circle cx="20" cy="80" r="3"/><circle cx="50" cy="80" r="3"/><circle cx="80" cy="80" r="3"/>
      <circle cx="20" cy="110" r="3"/><circle cx="50" cy="110" r="3"/>
    </g>
  </svg>
  <h2>Join Now</h2>
  <p class="lead">Lorem ipsum dolor sit amet, consectetur adipiscing</p>
  <a class="btn btn-solid" href="#">Learn More</a>
  <div class="social" aria-label="Social links"><span></span><span></span><span></span></div>
  <p class="copyright">&copy;Copyrights 2021 Company Name &nbsp;|&nbsp; All Rights Reserved</p>
</footer>

</body>
</html>
```